Client Fulfillment Flyer

This is a document used for internal purposes ie it is not distributed to clients. We would like it to have some colour, images etc. We are in the financial services industry, Ballarat, Victoria, Australia. www.torvenfield.com.au and www.torvenfieldagri.com.au

Target Market(s)

Internal training document

Industry/Entity Type

Finance And Accounting

Colors
3176b5

```html
<!DOCTYPE html>
<html lang="en">
<head>
<meta charset="utf-8">
<title>Torvenfield &amp; Co – Client Fulfillment</title>
<link href="https://fonts.googleapis.com/css2?family=Source+Sans+3:wght@400;600&display=swap" rel="stylesheet">
<style>
  :root {
    --brand: #1a62d8;
    --ink: #4a5058;
    --rule: #e3e6ea;
    --frame: #3a3d42;
    --paper: #ffffff;
  }
  * { margin: 0; padding: 0; box-sizing: border-box; }
  html, body { width: 939px; height: 1200px; overflow: hidden; background: var(--paper); }
  .page {
    position: relative; width: 939px; height: 1200px;
    font-family: "Source Sans 3", "Source Sans Pro", sans-serif;
    color: var(--ink); font-size: 13.6px; line-height: 20px;
    border-right: 1.5px solid var(--frame); border-bottom: 1.5px solid var(--frame);
  }
  .header-rule { position: absolute; left: 78px; top: 76px; width: 600px; height: 1px; background: var(--rule); }
  .brand { position: absolute; left: 685px; top: 60px; display: flex; align-items: center; gap: 7px; }
  .brand-dot { width: 32px; height: 32px; border-radius: 50%; background: var(--brand); }
  .brand-name { font-weight: 600; font-size: 19px; color: var(--brand); letter-spacing: 0.5px; text-transform: uppercase; }
  .content { position: absolute; left: 142px; top: 149px; width: 656px; }
  .section-title { color: var(--brand); font-weight: 400; font-size: 17.6px; line-height: 24px; margin-bottom: 15px; }
  .section-title.second { margin-top: 31px; }
  .rules { list-style: none; }
  .rules li { text-align: justify; margin-bottom: 15px; }
  .rules .num { display: inline-block; width: 52px; }
  .auto-reply { color: var(--brand); text-align: center; margin: 17px 0 15px; }
  .content p.body { text-align: justify; margin-bottom: 15px; }
  .footer-rule { position: absolute; left: 77px; top: 1125px; width: 794px; height: 1px; background: var(--rule); }
  .page-badge {
    position: absolute; left: 446px; top: 1102px; width: 46px; height: 46px; border-radius: 50%;
    background: var(--paper); border: 1px solid var(--rule);
    display: flex; align-items: center; justify-content: center;
  }
  .page-num {
    width: 32px; height: 32px; border-radius: 50%; background: var(--brand); color: #fff;
    font-size: 16px; display: flex; align-items: center; justify-content: center;
  }
</style>
</head>
<body>
<div class="page">
  <div class="header-rule"></div>
  <div class="brand"><span class="brand-dot"></span><span class="brand-name">Torvenfield &amp; Co</span></div>

  <main class="content">
    <h2 class="section-title">The 10 Non Negotiables:</h2>
    <ol class="rules">
      <li><span class="num">1.</span>Client phone calls and emails are replied to the same day received. Even if to say, received call/email will respond …. OR have CSM contact client on your behalf.</li>
      <li><span class="num">2.</span>Work is allocated / delegated to the appropriate team member.</li>
      <li><span class="num">3.</span>Systems, processes and checklists are used.</li>
      <li><span class="num">4.</span>All compliance work and lodgments are completed on time and by due dates.</li>
      <li><span class="num">5.</span>A fee proposal is communicated to client before starting work if it is not already covered by the annual fee agreement.</li>
      <li><span class="num">6.</span>The AYFS requirements are completed and updated annually (normally with Annual Accounts meeting).</li>
      <li><span class="num">7.</span>Annual Accounts meeting occurs once annual financial statements and taxation returns are completed.</li>
      <li><span class="num">8.</span>There is a minimum of monthly communication to clients under management.</li>
      <li><span class="num">9.</span>Prior to going on leave client work is planned and necessary arrangements are put in place to ensure clients under management are being looked after.&nbsp; This includes an automated email response as follows:
        <p class="auto-reply">Thank you for your email.&nbsp; I am currently on leave until ENTER DATE.&nbsp; I may not have email access<br>whilst away so please contact the following team members for assistance.<br>ACCOUNTANT NAME &amp; EMAIL ADDRESS, CSM NAME &amp; EMAIL ADDRESS</p>
      </li>
      <li><span class="num">10.</span>We are outcome focused rather than timesheet focused.</li>
    </ol>

    <h2 class="section-title second">The Right People Doing the Right Work</h2>
    <p class="body">A team is a group of individuals all working together for a common purpose.&nbsp; Each team member has a role in the team to achieve the goal or result.</p>
    <p class="body">To deliver Client Fulfillment it is important that we work as a team and understand our role and the tasks attached to that role.</p>
    <p class="body">This will ensure as a team we are directing our time and focus in the way required to have the capacity to deliver Client Fulfillment.</p>
    <p class="body">Much of our time is invested completing The Basics.&nbsp; However on a daily basis there is so much more to do to help clients and having the capacity is to complete this additional work is vital to delivering Client Fulfillment.</p>
  </main>

  <div class="footer-rule"></div>
  <div class="page-badge"><span class="page-num">4</span></div>
</div>
</body>
</html>
```